MES Modul-Struktur grafisch veranschaulichen
Zielgruppe
Wir sind Software-Hersteller. Thema 'MES'. Unsere Kunden sind Produktionsunternehmen.
Mit einem MES (Manufacturing Execution System) werden Produktionsprozesse überwacht, geplant, gesteuert und optimiert. Allgemein geht es darum, die Produktivität zu steigern und Kosten zu minimieren.
Eine MES-Software ist modular strukturiert, so dass der Kunde sich nach Bedarf die einzelnen Funktionsmodule zusammenstellen kann. Unser MES KORVIN 7 MAX besteht z.B. aus folgenden Einzelmodulen:
- BASIS (Basismodul)
- MDE (Maschinendatenerfassung)
- BDE (Betriebsdatenerfassung)
- INST (Instandhaltung)
- ALARM (Alarmierung)
- DOK (Dokumentenmanagement)
- TNT (Traceability)
- PLAN (Feinplanung/Leitstand)
- LOG (Logistik)
- VIS (Visualisierung)
- PEP (Personaleinsatzplanung)
- MPZE (Personalzeiterfassung)
- DNC (Rezepturen/DNC)
- EM (Energiemonitoring)
Aufgabenstellung
Die modulare Struktur und der große Umfang an Modulen ist ein wichtiger Vorteil für unsere Kunden, da Sie nicht so schnell an Grenzen stoßen und sich dann unter Umständen eine weitere Insellösung (extra Software mit extra Datenbank ...) anschaffen müssen.
Wichtig ist, dass die einzelnen Module funktionell ineinandergreifen und alle auf die gleiche Datenbank zugreifen.
Es reicht wenn in der Grafik die Module nur mit er Abkürzung, also z.B. MDE bezeichnet werden. Für den ersten Entwurf können auch Platzhalter genutzt werden.
Der Betrachter sollte aus der Grafik auf den ersten Blick erkennen:
- umfängliches MES
- modular strukturiert
- Funktionsmodule step-by-step erweiterbar
Für die Umsetzung naheliegend wären Puzzle-Steine, Blokkis, ... muss aber nicht.

```html
<!DOCTYPE html>
<html lang="de">
<head>
<meta charset="utf-8">
<title>MES Modulstruktur</title>
<link href="https://fonts.googleapis.com/css2?family=Source+Sans+3:wght@400;600;700&display=swap" rel="stylesheet">
<style>
  :root{
    --bg:#ffffff;
    --band:#c3d1db;
    --line:#c8d5de;
    --ring:#cbd7df;
    --legend-bg:#ffffff;
    --legend-border:#9fb0bc;
    --text:#1d1d1b;
    --basis:#c3d1db;
    --mde:#f2b300;
    --bde:#ec7b12;
    --inst:#e2541d;
    --alarm:#a0c31f;
    --dok:#5aa733;
    --tnt:#1c9a3c;
    --plan:#1e7b3b;
    --log:#0e5a2f;
    --vis:#7fc4e9;
    --pep:#2f8fd1;
    --mpze:#1f4f9d;
    --dnc:#7b2b7b;
    --em:#4b2a6f;
  }
  html,body{margin:0;padding:0;background:var(--bg);}
  body{width:848px;height:1200px;overflow:hidden;font-family:"Source Sans 3",Arial,sans-serif;}
  .diagram{display:block;width:848px;height:1200px;}
  .connector{fill:none;stroke:var(--line);stroke-width:6;stroke-linejoin:miter;}
  .ring{fill:var(--ring);}
  .core{stroke:#fff;stroke-width:3;}
  .abbr{fill:#fff;font-weight:700;font-size:15px;text-anchor:middle;letter-spacing:.2px;}
  .icon{fill:none;stroke:#fff;stroke-width:1.8;stroke-linecap:round;stroke-linejoin:round;}
  .icon-fill{fill:#fff;stroke:none;}
  .basis-label{fill:#fff;font-weight:700;font-size:15px;text-anchor:middle;}
  .legend-box{fill:var(--legend-bg);stroke:var(--legend-border);stroke-width:1;}
  .legend-abbr{font-weight:700;font-size:14px;fill:var(--text);}
  .legend-desc{font-size:15.5px;fill:var(--text);}
</style>
</head>
<body>
<svg class="diagram" viewBox="0 0 595 842" xmlns="http://www.w3.org/2000/svg" role="img" aria-label="MES Modulbaum: alle Funktionsmodule wachsen aus dem Basismodul">
  <defs>
    <filter id="legend-shadow" x="-5%" y="-5%" width="110%" height="115%">
      <feDropShadow dx="0" dy="1" stdDeviation="1.5" flood-color="#5b6b76" flood-opacity=".35"/>
    </filter>
  </defs>

  <rect class="base-band" x="0" y="578" width="595" height="264" fill="var(--band)"/>

  <g class="connectors">
    <path class="connector" d="M320 60 V578"/>
    <path class="connector" d="M270 145 V578"/>
    <path class="connector" d="M372 155 V205 H312 V578"/>
    <path class="connector" d="M175 180 V238 H292 V578"/>
    <path class="connector" d="M130 292 H236 V350 H285 V578"/>
    <path class="connector" d="M85 395 H278 V578"/>
    <path class="connector" d="M205 445 V462 H299 V578"/>
    <path class="connector" d="M130 518 H264 V578"/>
    <path class="connector" d="M458 205 V380 H327 V578"/>
    <path class="connector" d="M382 280 V482 H306 V578"/>
    <path class="connector" d="M520 330 H452 V390 H334 V578"/>
    <path class="connector" d="M520 436 H341 V578"/>
    <path class="connector" d="M430 520 V506 H348 V578"/>
  </g>

  <g class="module module-em" transform="translate(320 60)">
    <circle class="ring" r="37"/><circle class="core" r="30" fill="var(--em)"/>
    <text class="abbr" y="-3">EM</text>
    <rect class="icon" x="-10" y="5" width="18" height="11" rx="1.5"/>
    <rect class="icon-fill" x="8.5" y="8" width="3" height="5"/>
    <rect class="icon-fill" x="-7.5" y="7.5" width="8" height="6"/>
  </g>

  <g class="module module-pep" transform="translate(270 145)">
    <circle class="ring" r="37"/><circle class="core" r="30" fill="var(--pep)"/>
    <text class="abbr" y="-3">PEP</text>
    <g class="icon-fill">
      <circle cx="-8" cy="5" r="2.6"/><rect x="-11" y="8.5" width="6" height="9" rx="2"/>
      <circle cx="0" cy="4" r="2.8"/><rect x="-3.3" y="7.8" width="6.6" height="10" rx="2"/>
      <circle cx="8" cy="5" r="2.6"/><rect x="5" y="8.5" width="6" height="9" rx="2"/>
    </g>
  </g>

  <g class="module module-dnc" transform="translate(372 155)">
    <circle class="ring" r="37"/><circle class="core" r="30" fill="var(--dnc)"/>
    <text class="abbr" y="-3">DNC</text>
    <g class="icon-fill">
      <rect x="-3" y="3" width="6" height="5"/>
      <rect x="-10" y="13" width="6" height="5"/><rect x="-3" y="13" width="6" height="5"/><rect x="4" y="13" width="6" height="5"/>
    </g>
    <path class="icon" d="M0 8 V13 M-7 13 V10.5 H7 V13" stroke-width="1.3"/>
  </g>

  <g class="module module-vis" transform="translate(175 180)">
    <circle class="ring" r="37"/><circle class="core" r="30" fill="var(--vis)"/>
    <text class="abbr" y="-3">VIS</text>
    <path class="icon" d="M-12 10 Q0 -1 12 10 Q0 21 -12 10 Z"/>
    <circle class="icon" cx="0" cy="10" r="4"/>
    <circle class="icon-fill" cx="0" cy="10" r="1.8"/>
  </g>

  <g class="module module-mpze" transform="translate(458 205)">
    <circle class="ring" r="37"/><circle class="core" r="30" fill="var(--mpze)"/>
    <text class="abbr" y="-3">MPZE</text>
    <circle class="icon" cx="0" cy="10" r="8.5"/>
    <path class="icon" d="M0 5 V10 H4"/>
  </g>

  <g class="module module-plan" transform="translate(382 280)">
    <circle class="ring" r="37"/><circle class="core" r="30" fill="var(--plan)"/>
    <text class="abbr" y="-3">PLAN</text>
    <rect class="icon" x="-10" y="3" width="20" height="15" rx="1.5"/>
    <path class="icon" d="M-10 7 H10 M-5 1 V4.5 M5 1 V4.5"/>
    <g class="icon-fill">
      <rect x="-7" y="9" width="3" height="2.5"/><rect x="-1.5" y="9" width="3" height="2.5"/><rect x="4" y="9" width="3" height="2.5"/>
      <rect x="-7" y="13" width="3" height="2.5"/><rect x="-1.5" y="13" width="3" height="2.5"/><rect x="4" y="13" width="3" height="2.5"/>
    </g>
  </g>

  <g class="module module-log" transform="translate(130 292)">
    <circle class="ring" r="37"/><circle class="core" r="30" fill="var(--log)"/>
    <text class="abbr" y="-3">LOG</text>
    <g class="icon-fill">
      <rect x="-13" y="3" width="16" height="11" rx="1"/>
      <path d="M4 6 H9 L13 10 V14 H4 Z"/>
    </g>
    <circle cx="-8" cy="15.5" r="2.6" fill="#fff" stroke="var(--log)" stroke-width="1.2"/>
    <circle cx="8" cy="15.5" r="2.6" fill="#fff" stroke="var(--log)" stroke-width="1.2"/>
  </g>

  <g class="module module-tnt" transform="translate(520 330)">
    <circle class="ring" r="37"/><circle class="core" r="30" fill="var(--tnt)"/>
    <text class="abbr" y="-3">TNT</text>
    <path class="icon" d="M-11 5 H-5 L5 15 H10 M-11 15 H-5 L5 5 H10 M7 2 L10 5 L7 8 M7 12 L10 15 L7 18"/>
  </g>

  <g class="module module-dok" transform="translate(85 385)">
    <circle class="ring" r="37"/><circle class="core" r="30" fill="var(--dok)"/>
    <text class="abbr" y="-3">DOK</text>
    <path class="icon" d="M-7 2 H3 L8 7 V20 H-7 Z M3 2 V7 H8"/>
    <path class="icon" d="M-4 11 H5 M-4 14 H5 M-4 17 H5" stroke-width="1.3"/>
  </g>

  <g class="module module-inst" transform="translate(520 436)">
    <circle class="ring" r="37"/><circle class="core" r="30" fill="var(--inst)"/>
    <text class="abbr" y="-3">INST</text>
    <path class="icon" d="M-9 19 L6 4 M-10 4 L7 19" stroke-width="2.6"/>
    <circle class="icon" cx="7" cy="3" r="3"/>
  </g>

  <g class="module module-alarm" transform="translate(205 445)">
    <circle class="ring" r="37"/><circle class="core" r="30" fill="var(--alarm)"/>
    <text class="abbr" y="-3">ALARM</text>
    <circle class="icon-fill" cx="0" cy="11" r="3"/>
    <path class="icon" d="M-6 5 A8 8 0 0 0 -6 17 M6 5 A8 8 0 0 1 6 17 M-10 2 A12 12 0 0 0 -10 20 M10 2 A12 12 0 0 1 10 20"/>
  </g>

  <g class="module module-mde" transform="translate(130 518)">
    <circle class="ring" r="37"/><circle class="core" r="30" fill="var(--mde)"/>
    <text class="abbr" y="-3">MDE</text>
    <circle class="icon" cx="-5" cy="7" r="4.5" stroke-dasharray="2 1.5" stroke-width="2.6"/>
    <circle class="icon" cx="-5" cy="7" r="1.6"/>
    <circle class="icon" cx="-4" cy="16" r="3" stroke-dasharray="1.6 1.2" stroke-width="2.2"/>
    <path class="icon" d="M3 18 L11 8 L13 10 L5 20 L2.5 20.5 Z"/>
  </g>

  <g class="module module-bde" transform="translate(430 520)">
    <circle class="ring" r="37"/><circle class="core" r="30" fill="var(--bde)"/>
    <text class="abbr" y="-3">BDE</text>
    <path class="icon" d="M-11 3 V19 H11"/>
    <path class="icon" d="M-7 18 V11 M-3 18 V7" stroke-width="2.2"/>
    <circle class="icon" cx="4" cy="9" r="4"/>
    <path class="icon" d="M7 12 L10 16"/>
  </g>

  <text class="basis-label" x="297" y="606">BASIS</text>
  <path class="pin" d="M297 640 C291.5 632.5 288 628.5 288 624 A9 9 0 0 1 306 624 C306 628.5 302.5 632.5 297 640 Z" fill="#fff"/>
  <circle cx="297" cy="624" r="3" fill="var(--band)"/>

  <rect class="legend-box" x="25" y="651" width="547" height="171" rx="4" filter="url(#legend-shadow)"/>
  <g class="legend">
    <g transform="translate(0 670)">
      <circle cx="50" cy="0" r="3.2" fill="var(--basis)"/><text class="legend-abbr" x="58" y="5">BASIS</text><text class="legend-desc" x="120" y="5">Basismodul</text>
      <circle cx="330" cy="0" r="3.2" fill="var(--plan)"/><text class="legend-abbr" x="338" y="5">PLAN</text><text class="legend-desc" x="392" y="5">Feinplanung/Leitstand</text>
    </g>
    <g transform="translate(0 692)">
      <circle cx="50" cy="0" r="3.2" fill="var(--mde)"/><text class="legend-abbr" x="58" y="5">MDE</text><text class="legend-desc" x="120" y="5">Maschinendatenerfassung</text>
      <circle cx="330" cy="0" r="3.2" fill="var(--log)"/><text class="legend-abbr" x="338" y="5">LOG</text><text class="legend-desc" x="392" y="5">Logistik</text>
    </g>
    <g transform="translate(0 714)">
      <circle cx="50" cy="0" r="3.2" fill="var(--bde)"/><text class="legend-abbr" x="58" y="5">BDE</text><text class="legend-desc" x="120" y="5">Betriebsdatenerfassung</text>
      <circle cx="330" cy="0" r="3.2" fill="var(--vis)"/><text class="legend-abbr" x="338" y="5">VIS</text><text class="legend-desc" x="392" y="5">Visualisierung</text>
    </g>
    <g transform="translate(0 736)">
      <circle cx="50" cy="0" r="3.2" fill="var(--inst)"/><text class="legend-abbr" x="58" y="5">INST</text><text class="legend-desc" x="120" y="5">Instandhaltung</text>
      <circle cx="330" cy="0" r="3.2" fill="var(--pep)"/><text class="legend-abbr" x="338" y="5">PEP</text><text class="legend-desc" x="392" y="5">Personaleinsatzplanung</text>
    </g>
    <g transform="translate(0 758)">
      <circle cx="50" cy="0" r="3.2" fill="var(--alarm)"/><text class="legend-abbr" x="58" y="5">ALARM</text><text class="legend-desc" x="120" y="5">Alarmierung</text>
      <circle cx="330" cy="0" r="3.2" fill="var(--mpze)"/><text class="legend-abbr" x="338" y="5">MPZE</text><text class="legend-desc" x="392" y="5">Personalzeiterfassung</text>
    </g>
    <g transform="translate(0 780)">
      <circle cx="50" cy="0" r="3.2" fill="var(--dok)"/><text class="legend-abbr" x="58" y="5">DOK</text><text class="legend-desc" x="120" y="5">Dokumentenmanagement</text>
      <circle cx="330" cy="0" r="3.2" fill="var(--dnc)"/><text class="legend-abbr" x="338" y="5">DNC</text><text class="legend-desc" x="392" y="5">Rezepturen/DNC</text>
    </g>
    <g transform="translate(0 802)">
      <circle cx="50" cy="0" r="3.2" fill="var(--tnt)"/><text class="legend-abbr" x="58" y="5">TNT</text><text class="legend-desc" x="120" y="5">Traceability</text>
      <circle cx="330" cy="0" r="3.2" fill="var(--em)"/><text class="legend-abbr" x="338" y="5">EM</text><text class="legend-desc" x="392" y="5">Energiemonitoring</text>
    </g>
  </g>
</svg>
</body>
</html>
```